BOLD & MINIMALIST DESIGN NEEDED

We want a very bold but minimalistic business card design that is impactful and utilizes both sides of the business card. Our current logo is included for your use.

We want bold fonts and good use of negative space. We don't want the logo to overpower the design.

Target Market(s)

Professionals who are building new commercial buildings.

Industry/Entity Type

Construction

Contact Information for Business Card

Name, Title, email, office phone, cell phone, website

Font styles to use
Serif
Sans Serif

Requirements
Must have
• Bold design!

```html
<!DOCTYPE html>
<html lang="en">
<head>
<meta charset="utf-8">
<title>Stonebridge – Business Card</title>
<link rel="stylesheet" href="https://fonts.googleapis.com/css2?family=Arimo:wght@400;700&display=swap">
<style>
  :root {
    --backdrop: #e4e4e4;
    --card-white: #ffffff;
    --card-dark: #2f2f2f;
    --ink: #111111;
    --ink-soft: #444444;
    --green: #7dc242;
    --green-light: #b5e07f;
    --white: #ffffff;
  }
  * { box-sizing: border-box; margin: 0; padding: 0; }
  html, body { width: 1200px; height: 1200px; overflow: hidden; }
  body {
    background: var(--backdrop);
    font-family: "Arimo", Arial, sans-serif;
    position: relative;
  }
  .card {
    position: absolute;
    width: 689px;
    height: 393px;
    overflow: hidden;
  }
  .card-front { left: 267px; top: 159px; background: var(--card-white); }
  .card-back { left: 262px; top: 653px; background: var(--card-dark); }

  /* front */
  .brand {
    position: absolute; left: 45px; top: 124px;
    display: flex; align-items: center; gap: 10px;
  }
  .brand-square { width: 22px; height: 22px; background: var(--green); }
  .brand-name {
    font-weight: 700; font-size: 28px; color: var(--ink); letter-spacing: 0.5px;
  }
  .person-name {
    position: absolute; left: 45px; top: 204px;
    font-weight: 700; font-size: 27px; color: var(--ink); letter-spacing: 0.3px;
  }
  .person-title {
    position: absolute; left: 45px; top: 234px;
    font-size: 16px; color: var(--green);
  }
  .contact-list {
    position: absolute; left: 45px; top: 272px; list-style: none;
  }
  .contact-list li {
    display: flex; align-items: center; gap: 12px;
    height: 20.5px; font-size: 16px; color: var(--ink-soft);
  }
  .contact-list svg { width: 14px; height: 14px; fill: var(--ink); flex: none; }
  .feature-block {
    position: absolute; left: 330px; top: 40px; width: 310px; height: 310px;
    background: linear-gradient(160deg, var(--green-light), var(--green));
  }
  .front-arc { position: absolute; left: 0; top: 0; }

  /* back */
  .back-brand {
    position: absolute; left: 0; right: 0; top: 200px;
    display: flex; justify-content: center; align-items: center; gap: 12px;
  }
  .back-brand .brand-square { width: 26px; height: 26px; }
  .back-brand .brand-name { color: var(--white); font-size: 34px; }
  .back-arc { position: absolute; left: 0; top: 0; }
  .back-url {
    position: absolute; left: 0; right: 0; top: 331px; text-align: center;
    font-size: 16px; letter-spacing: 3.2px; color: var(--white);
  }
  .back-url .accent { color: var(--green); font-weight: 700; }
</style>
</head>
<body>
  <section class="card card-front">
    <div class="brand">
      <span class="brand-square"></span>
      <span class="brand-name">STONEBRIDGE</span>
    </div>
    <h1 class="person-name">DANIEL REYES</h1>
    <p class="person-title">President</p>
    <ul class="contact-list">
      <li><svg viewBox="0 0 24 24"><path d="M6.6 10.8a15 15 0 0 0 6.6 6.6l2.2-2.2a1 1 0 0 1 1-.25 11.4 11.4 0 0 0 3.6.57 1 1 0 0 1 1 1V20a1 1 0 0 1-1 1A17 17 0 0 1 3 4a1 1 0 0 1 1-1h3.5a1 1 0 0 1 1 1c0 1.25.2 2.45.57 3.57a1 1 0 0 1-.25 1z"/></svg>555-214-3870</li>
      <li><svg viewBox="0 0 24 24"><path d="M7 1h10a2 2 0 0 1 2 2v18a2 2 0 0 1-2 2H7a2 2 0 0 1-2-2V3a2 2 0 0 1 2-2zm0 3v15h10V4z"/></svg>555-619-4452</li>
      <li><svg viewBox="0 0 24 24"><path d="M2 5h20v14H2zm2 2v.5l8 5 8-5V7zm0 3v7h16v-7l-8 5z"/></svg>info@stonebridge.com</li>
      <li><svg viewBox="0 0 24 24"><path d="M12 2a10 10 0 1 0 0 20 10 10 0 0 0 0-20zm-1 17.9A8 8 0 0 1 4.2 10.4L9 15v1a2 2 0 0 0 2 2zm6.9-2.5A2 2 0 0 0 16 16h-1v-3a1 1 0 0 0-1-1H8v-2h2a1 1 0 0 0 1-1V7h2a2 2 0 0 0 2-2v-.4a8 8 0 0 1 2.9 12.8z"/></svg>www.stonebridge.com</li>
    </ul>
    <div class="feature-block" role="img" aria-label="Large brand block in green tones"></div>
    <svg class="front-arc" width="689" height="393" viewBox="0 0 689 393">
      <path d="M222 393 Q440 340 689 384 L689 393 Z" fill="var(--ink)"/>
    </svg>
  </section>

  <section class="card card-back">
    <div class="back-brand">
      <span class="brand-square"></span>
      <span class="brand-name">STONEBRIDGE</span>
    </div>
    <svg class="back-arc" width="689" height="393" viewBox="0 0 689 393">
      <path d="M144 303 Q342 220 541 303 Q342 245 144 303 Z" fill="var(--white)"/>
    </svg>
    <p class="back-url">www.<span class="accent">stonebridge</span>.com</p>
  </section>
</body>
</html>
```